QVR business card

Need a business card for a company that provides instructional design and elearning development services. The website is here: http://quorvane.studio/

I'm attaching a current logo, as well as the old business card design. While I like to keep it clean, the old design is too simplistic for my liking. The only idea I want to reuse from the old design is placing industry jargon on the back of the card, just need a better way to present it. But if you have other ideas for the back--feel free to experiment.

Please use the colors complementary to the color we have on the website. Thank you!

```html
<!DOCTYPE html>
<html lang="en">
<head>
<meta charset="utf-8">
<title>QVR business card</title>
<link href="https://fonts.googleapis.com/css2?family=Source+Sans+3:wght@400;600&display=swap" rel="stylesheet">
<style>
  :root {
    --stage: #2b2b2b;
    --card: #111111;
    --card-edge: #1c1c1c;
    --teal: #3cc3b3;
    --sand: #e4d69c;
    --ink: #e9e9e9;
    --muted: #3a3a3a;
  }
  * { box-sizing: border-box; margin: 0; padding: 0; }
  html, body {
    width: 1200px; height: 900px; overflow: hidden;
    background: var(--stage);
    font-family: "Source Sans 3", "Myriad Pro", Arial, sans-serif;
  }
  .sheet {
    position: relative; width: 1200px; height: 900px;
    display: flex; align-items: center; justify-content: center; gap: 60px;
  }
  .card {
    position: relative; width: 520px; height: 300px;
    background: var(--card); border-radius: 22px;
    border: 1px solid var(--card-edge);
    box-shadow: 0 10px 30px rgba(0,0,0,.45);
    overflow: hidden;
  }
  /* front */
  .front .brand {
    position: absolute; left: 50px; top: 110px;
    display: flex; align-items: center; gap: 12px;
  }
  .brand-dot { width: 18px; height: 18px; border-radius: 50%; background: var(--teal); }
  .brand-name {
    font-weight: 600; font-size: 56px; letter-spacing: 2px; color: var(--sand); line-height: 1;
  }
  .front .divider {
    position: absolute; left: 245px; top: 40px; width: 1px; height: 220px; background: var(--muted);
  }
  .front .details { position: absolute; left: 275px; top: 92px; }
  .person {
    font-weight: 600; font-size: 21px; color: var(--teal); margin-bottom: 26px;
  }
  .contact-list { list-style: none; }
  .contact-list li {
    display: flex; align-items: center; gap: 8px;
    font-size: 16px; color: var(--ink); line-height: 22px;
  }
  .contact-list svg { width: 12px; height: 12px; flex: none; }
  /* back */
  .back .brand {
    position: absolute; left: 44px; top: 120px;
    display: flex; align-items: center; gap: 10px;
  }
  .back .brand-name { font-size: 50px; }
  .back .services { position: absolute; left: 265px; top: 58px; }
  .services-title {
    font-weight: 600; font-size: 20px; color: var(--teal); margin-bottom: 8px;
  }
  .service-list { list-style: none; }
  .service-list li {
    display: flex; align-items: center; gap: 10px;
    font-size: 14.5px; color: var(--ink); line-height: 23px;
  }
  .bullet { width: 9px; height: 9px; background: var(--teal); flex: none; }
</style>
</head>
<body>
<main class="sheet">
  <section class="card front" aria-label="Card front">
    <div class="brand">
      <span class="brand-dot"></span>
      <span class="brand-name">QVR</span>
    </div>
    <div class="divider"></div>
    <div class="details">
      <p class="person">Marek Valdessen</p>
      <ul class="contact-list">
        <li>
          <svg viewBox="0 0 12 12" aria-hidden="true"><path d="M2.5 1 L4.5 1 L5 3.5 L3.8 4.6 Q5 7 7.4 8.2 L8.5 7 L11 7.5 L11 9.5 Q10.5 11 9 11 Q1 10 1 2.5 Q1 1 2.5 1Z" fill="var(--teal)"/></svg>
          555-014-2286
        </li>
        <li>
          <svg viewBox="0 0 12 12" aria-hidden="true"><rect x="0.5" y="2" width="11" height="8" rx="1" fill="var(--teal)"/><path d="M1 2.5 L6 6.5 L11 2.5" stroke="var(--card)" fill="none"/></svg>
          mvaldessen@quorvane.studio
        </li>
        <li>
          <svg viewBox="0 0 12 12" aria-hidden="true"><circle cx="6" cy="6" r="5.5" fill="var(--teal)"/><path d="M0.5 6 H11.5 M6 0.5 Q2.5 6 6 11.5 M6 0.5 Q9.5 6 6 11.5" stroke="var(--card)" stroke-width="0.8" fill="none"/></svg>
          www.quorvane.studio
        </li>
      </ul>
    </div>
  </section>

  <section class="card back" aria-label="Card back">
    <div class="brand">
      <span class="brand-name">QVR</span>
    </div>
    <div class="services">
      <p class="services-title">How can we help?</p>
      <ul class="service-list">
        <li><span class="bullet"></span>Mobile Learning Scorm</li>
        <li><span class="bullet"></span>Instructional Design Lms</li>
        <li><span class="bullet"></span>Moocs Elearning Html5</li>
        <li><span class="bullet"></span>Adult Learning Theory</li>
        <li><span class="bullet"></span>Gamification Classroom</li>
        <li><span class="bullet"></span>Xapi Blended Learning</li>
      </ul>
    </div>
  </section>
</main>
</body>
</html>
```